Business Card Design for Property Development Company Director

I am looking for a professional and unforgettable business card design for our Director of our Property Development Company.
Please see attached .pptx file to find out what information to include. You don't have to follow the exact format shown in the file - I am interested to see your creative flair using the information provided.

```html
<!DOCTYPE html>
<html lang="en">
<head>
<meta charset="utf-8">
<title>Norvale Property Group – Business Card</title>
<link href="https://fonts.googleapis.com/css2?family=Montserrat:wght@600;700&family=Open+Sans:wght@400;600&display=swap" rel="stylesheet">
<style>
  :root {
    --stage: #2a2a2c;
    --brand-blue: #0f56a6;
    --ink-grey: #5b5b5d;
    --band-grey: #6f6f71;
    --paper: #ffffff;
    --text-dark: #3a3a3c;
  }
  * { box-sizing: border-box; margin: 0; padding: 0; }
  html, body { width: 1200px; height: 895px; overflow: hidden; }
  body {
    background: var(--stage);
    font-family: "Open Sans", Arial, sans-serif;
    display: flex; flex-direction: column; align-items: center; justify-content: center;
    gap: 40px;
  }
  .card {
    width: 640px; height: 366px; position: relative; overflow: hidden;
    box-shadow: 0 10px 30px rgba(0,0,0,.45);
  }
  /* Front */
  .card--front { background: var(--brand-blue); color: var(--paper); }
  .brand {
    display: flex; align-items: center; gap: 18px;
    font-family: "Montserrat", Arial, sans-serif; font-weight: 700;
  }
  .brand__square { width: 62px; height: 62px; flex: none; }
  .brand__name { line-height: 1.05; font-size: 30px; letter-spacing: 1px; }
  .card--front .brand { position: absolute; left: 150px; top: 92px; }
  .card--front .brand__square { background: var(--paper); }
  .tagline {
    position: absolute; left: 150px; top: 182px;
    font-size: 15px; letter-spacing: .3px;
  }
  .invite {
    position: absolute; left: 40px; bottom: 44px;
    font-size: 16px; letter-spacing: .4px;
  }
  /* Back */
  .card--back { background: var(--paper); }
  .card--back .brand { position: absolute; left: 230px; top: 40px; color: var(--brand-blue); }
  .card--back .brand__square { background: var(--brand-blue); width: 54px; height: 54px; }
  .card--back .brand__name { font-size: 26px; }
  .person {
    position: absolute; right: 372px; top: 150px; text-align: right;
  }
  .person__name {
    font-family: "Montserrat", Arial, sans-serif; font-weight: 700;
    font-size: 27px; color: var(--brand-blue); letter-spacing: .3px;
  }
  .person__role { font-size: 17px; color: var(--text-dark); margin-top: 2px; }
  .divider {
    position: absolute; left: 286px; top: 136px; width: 2px; height: 86px;
    background: var(--ink-grey);
  }
  .contacts {
    position: absolute; left: 308px; top: 138px; list-style: none;
    font-size: 17px; color: var(--text-dark);
  }
  .contacts li { display: flex; align-items: center; gap: 10px; height: 28px; }
  .contacts svg { width: 15px; height: 15px; fill: var(--brand-blue); flex: none; }
  .licence-band {
    position: absolute; left: 0; right: 0; bottom: 44px; height: 44px;
    background: var(--band-grey); color: var(--paper);
    display: flex; align-items: center; justify-content: flex-end;
    padding-right: 48px; font-size: 17px; letter-spacing: .4px;
  }
</style>
</head>
<body>
  <section class="card card--front">
    <div class="brand">
      <span class="brand__square"></span>
      <span class="brand__name">NORVALE<br>PROPERTY GROUP</span>
    </div>
    <p class="tagline">Property Development &amp; Site Acquisition Specialists</p>
    <p class="invite">Ask me about our INVESTMENT &amp; PARTNERSHIP opportunities</p>
  </section>

  <section class="card card--back">
    <div class="brand">
      <span class="brand__square"></span>
      <span class="brand__name">NORVALE<br>PROPERTY GROUP</span>
    </div>
    <div class="person">
      <p class="person__name">DANIEL MERCER</p>
      <p class="person__role">Director</p>
    </div>
    <span class="divider"></span>
    <ul class="contacts">
      <li>
        <svg viewBox="0 0 24 24" aria-hidden="true"><path d="M6.6 10.8a15.1 15.1 0 0 0 6.6 6.6l2.2-2.2a1 1 0 0 1 1-.25 11.4 11.4 0 0 0 3.6.57 1 1 0 0 1 1 1V20a1 1 0 0 1-1 1A17 17 0 0 1 3 4a1 1 0 0 1 1-1h3.5a1 1 0 0 1 1 1c0 1.25.2 2.45.57 3.57a1 1 0 0 1-.25 1z"/></svg>
        0400 123 456
      </li>
      <li>
        <svg viewBox="0 0 24 24" aria-hidden="true"><path d="M2 5h20v14H2z" fill="none"/><path d="M2 5h20v2l-10 6L2 7zM2 9l10 6 10-6v10H2z"/></svg>
        daniel@norvale.com.au
      </li>
      <li>
        <svg viewBox="0 0 24 24" aria-hidden="true"><path d="M12 2a10 10 0 1 0 0 20 10 10 0 0 0 0-20zm6.9 6h-3a15.7 15.7 0 0 0-1.4-3.6A8 8 0 0 1 18.9 8zM12 4c.8 1.2 1.5 2.5 1.9 4h-3.8c.4-1.5 1.1-2.8 1.9-4zM4.3 14a8 8 0 0 1 0-4h3.4a16.5 16.5 0 0 0 0 4zm.8 2h3a15.7 15.7 0 0 0 1.4 3.6A8 8 0 0 1 5.1 16zm3-8h-3a8 8 0 0 1 4.4-3.6A15.7 15.7 0 0 0 8.1 8zM12 20c-.8-1.2-1.5-2.5-1.9-4h3.8c-.4 1.5-1.1 2.8-1.9 4zm2.3-6H9.7a14.7 14.7 0 0 1 0-4h4.6a14.7 14.7 0 0 1 0 4zm.2 5.6a15.7 15.7 0 0 0 1.4-3.6h3a8 8 0 0 1-4.4 3.6zm1.8-5.6a16.5 16.5 0 0 0 0-4h3.4a8 8 0 0 1 0 4z"/></svg>
        www.norvale.com.au
      </li>
    </ul>
    <div class="licence-band">Real Estate Lic: 5129036 &amp; 5129037</div>
  </section>
</body>
</html>
```